Market place for used airplanes/helicopters/parts

http://www.vingtorget.se needs a facelift.

# What is it
Classifieds for used airplanes/helicopters/parts/spare parts/aviation literature, for people in Scandinavia. The number of classifieds is ~120-200. They are mainly in Swedish, English, Norwegian.

It's not a glamorous or luxurious business, but more for people with a genuine interest in flying, technical things.

Similar to sites like this, but they have much more classifieds than my site
http://www.skyvendor.com/list/list.aspx?ETID=1&setype=1&catid=6
http://www.lindqvistflyg.com/planes.asp?meny=1&typ=single
https://www.hangarhub.com/cat.php?mode=listing&main=

# What I want
Design only - no code. I want a modern, maybe a bit bootstrap like, clean, simple, not flashy, web design. I want the design to be in English.

# Audience of the website
Aviation interested men, 45-65 years old, in the nordic countries (around Sweden).

# Logotype that could be used (but not necessarily)
http://www.vingtorget.se/flygplan_till_salu_large.jpg
http://www.vingtorget.se/flygplan_till_salu.eps

Reason: I decided to extend the deadline with 1 day. The reason is that I (unfortunately) managed to put the contest in the wrong category for 1 day + I want to give you all feedback (been too busy the whole day, sorry).

Hi all! 

Thanks everyone for the contributions you made. 

I will setup a poll for the designs that I like most. Will get back when I have more information. 

Thanks and have a nice weekend!
Erik

Target Market(s)

45-65 old Scandinavian men

Industry/Entity Type

Business

Requirements
Must have
• - A list with classifieds on the first page, so the visitor easily can see new classifieds.
- A classifieds should be able to have more than one photo
- A simple navigation for showing classifieds from categories like airplanes, helicopters/gyrocopters, parts, literature, misc (maybe other categories) .... but still, it's just 100-200 ads so it's not needed that much filtration.

- A placeholder/way of showing aviation news/clips. In the old design I had, it was a column to the right. It's enough to show maybe 2-5 placeholders.
- A placeholder for PlaceMint ads somewhere on the site.
Should not have
• - Carousels
- Too much clutter

```html
<!DOCTYPE html>
<html lang="en">
<head>
<meta charset="utf-8">
<title>Vingtorget – Aircraft for sale</title>
<link href="https://fonts.googleapis.com/css2?family=Roboto:wght@400;500&display=swap" rel="stylesheet">
<style>
:root{
  --blue:#1a64ad;
  --sky:#129fdf;
  --sky-dark:#0b8bcc;
  --navy:#0d5aa3;
  --text:#333;
  --muted:#444;
  --card:#f7f7f7;
  --line:#e1e1e1;
  --footer:#e8e8e8;
  --dark-box:#3d3d3d;
}
*{box-sizing:border-box;margin:0;padding:0}
html,body{width:960px;height:1200px;overflow:hidden}
body{font-family:'Roboto',sans-serif;color:var(--text);background:#fff;position:relative}
.wrap{position:absolute;left:104px;width:752px}

/* header */
.site-header{top:0;height:104px}
.brand{position:absolute;left:0;top:28px;display:flex;align-items:center;gap:8px}
.brand-mark{width:22px;height:22px;border-radius:50%;background:var(--sky)}
.brand-name{font-size:30px;font-weight:500;color:var(--blue);letter-spacing:1px}
.account{position:absolute;right:0;top:13px;height:30px;width:120px;background:var(--dark-box);border-radius:2px;color:#fff;font-size:10.5px;display:flex;align-items:center;justify-content:center;gap:6px;letter-spacing:.3px}
.account .login{color:#37aaf0}
.tagline{position:absolute;right:0;top:71px;font-size:18px;font-weight:400;color:#333;letter-spacing:.4px}
.tagline span{color:var(--blue)}

/* nav */
.main-nav{top:107px;height:36px;display:flex;background:linear-gradient(var(--sky),var(--sky-dark))}
.main-nav a{color:#fff;text-decoration:none;font-size:11.5px;letter-spacing:.3px;display:flex;align-items:center;padding:0 12.5px}
.main-nav .primary{display:flex;flex:1;padding-left:0}
.main-nav .actions{display:flex;background:var(--navy)}
.main-nav .actions a{padding:0 17px}
.main-nav .actions a+a{border-left:1px solid #0a4a88}

/* listings */
.col{position:absolute;top:157px;width:244px;display:flex;flex-direction:column;gap:16px}
.col-1{left:102px}.col-2{left:358px}.col-3{left:614px}
.listing{background:var(--card);border:1px solid var(--line);border-radius:2px;padding:7px 6px 8px}
.photos{display:flex;gap:6px}
.photos .side{display:flex;flex-direction:column;gap:6px}
.photo{display:block}
.stack{display:flex;flex-direction:column;gap:5px}
.stack .row{display:flex;gap:5px}
.listing h2{font-size:15px;font-weight:400;color:var(--blue);margin:11px 0 2px 3px}
.desc{font-size:10.5px;line-height:14px;margin-left:3px;color:var(--muted);max-width:205px}
.seller{display:flex;margin-top:2px;gap:10px;padding-left:3px}
.avatar{width:48px;height:46px;flex:none;margin-top:3px}
.seller ul{list-style:none;font-size:10.5px;line-height:18.5px}
.seller b{font-weight:400;color:var(--blue)}

/* side */
.promo{height:200px;border:3px solid #e9f08f;background:linear-gradient(135deg,#3aa1a0,#2e8a8c 60%,#d8c5b4)}
.news{background:#f4f4f4;border:1px solid var(--line)}
.news h3{height:30px;background:linear-gradient(var(--sky),var(--sky-dark));color:#fff;font-weight:400;font-size:15px;padding:6px 12px}
.news article{padding:8px 13px 7px;border-bottom:1px solid #d6d6d6;height:63px}
.news article:last-child{border-bottom:none}
.news h4{font-weight:400;font-size:12.5px;color:var(--blue)}
.news p{font-size:10.5px;line-height:14.5px;color:#555;margin-top:2px}
.ads{position:relative;height:197px;background:#fff;border:1px solid #888;border-radius:5px;margin:0 6px;padding:7px 12px;font-family:Arial,sans-serif}
.ad+.ad{margin-top:9px}
.ad a{font-size:11px;font-weight:bold;color:#0000cc;text-decoration:underline;letter-spacing:.3px}
.ad p{font-size:10px;line-height:12px;color:#111}
.ad small{font-size:7px;color:#008000;display:block;letter-spacing:.3px}
.ad-by{position:absolute;right:0;bottom:0;background:#111;color:#fff;font-size:8.5px;padding:2px 5px;border-radius:6px 0 4px 0}
.ad-choice{position:absolute;left:3px;bottom:3px;width:22px;height:9px;background:#aaa}

/* footer */
.site-footer{position:absolute;left:0;top:1090px;width:960px;height:110px;background:linear-gradient(#dcdcdc,#f2f2f2 30%,#f2f2f2)}
.copyright{position:absolute;left:105px;top:40px;font-size:10.5px;line-height:17px}
.copyright span{color:var(--blue)}
.follow{position:absolute;left:732px;top:18px}
.follow p{font-size:12px;color:#444}
.social{display:flex;gap:8px;margin-top:13px;margin-left:1px}
.social span{width:24px;height:24px;border-radius:3px;background:#5b86b8}
</style>
</head>
<body>

<header class="wrap site-header">
  <div class="brand"><span class="brand-mark"></span><span class="brand-name">VINGTORGET</span></div>
  <div class="account"><span>REGISTER</span><span>|</span><span class="login">LOG IN</span></div>
  <h1 class="tagline">AIRCRAFT FOR SALE - <span>THE LARGEST MARKET FOR FLIGHTS</span></h1>
</header>

<nav class="wrap main-nav">
  <div class="primary">
    <a href="#">AIRPLANES</a><a href="#">HELICOPTERS</a><a href="#">PARTS</a><a href="#">LITERATURE</a><a href="#">MISC</a><a href="#">SEARCH</a><a href="#">SUPPORT</a>
  </div>
  <div class="actions"><a href="#">UPLOAD</a><a href="#">CHANGE AD</a></div>
</nav>

<svg width="0" height="0" style="position:absolute">
  <defs>
    <symbol id="user" viewBox="0 0 48 46">
      <rect width="48" height="46" fill="#fff"/>
      <ellipse cx="25" cy="17" rx="10" ry="12" fill="#111"/>
      <path d="M4 46 C6 34 14 29 25 29 C36 29 44 34 46 46Z" fill="#111"/>
    </symbol>
  </defs>
</svg>

<main>
  <div class="col col-1">
    <article class="listing">
      <div class="photos">
        <div class="photo" role="img" aria-label="Yellow gyrocopter with two crew" style="width:147px;height:126px;background:linear-gradient(160deg,#8a9a7a,#c9c245 55%,#6b6b5c)"></div>
        <div class="side">
          <div class="photo" role="img" aria-label="Vacuum pump part" style="width:78px;height:60px;background:linear-gradient(#8c7b6a,#4c3d33)"></div>
          <div class="photo" role="img" aria-label="Gyrocopter accessories" style="width:78px;height:60px;background:linear-gradient(#cfcfcf,#3a3a3a)"></div>
        </div>
      </div>
      <h2>VACUUM PUMP</h2>
      <p class="desc">Nordic Pump Works, TT 222 hrs, price 1200 SEK</p>
      <div class="seller"><svg class="avatar" role="img" aria-label="Seller"><use href="#user"/></svg>
        <ul><li><b>Name:</b> Lars-Göran, Email</li><li><b>Phone:</b> 0700-318452</li><li><b>Date:</b> 2013-10-05 19:31:18</li></ul></div>
    </article>

    <article class="listing">
      <div class="stack">
        <div class="photo" role="img" aria-label="Red and yellow light aircraft on grass" style="width:225px;height:164px;margin-left:4px;background:linear-gradient(#8b8f7f,#b06a4a 50%,#5a5a4a)"></div>
        <div class="row" style="margin-left:4px">
          <div class="photo" role="img" aria-label="Cockpit instrument panel" style="width:110px;height:64px;background:linear-gradient(#777,#1e1e1e)"></div>
          <div class="photo" role="img" aria-label="Attitude indicator" style="width:110px;height:64px;background:linear-gradient(#b7bcc4,#6d7280)"></div>
        </div>
      </div>
      <h2>VACUUM PUMP</h2>
      <p class="desc">Nordic Pump Works, TT 222 hrs, price 1200 SEK</p>
      <div class="seller"><svg class="avatar" role="img" aria-label="Seller"><use href="#user"/></svg>
        <ul><li><b>Name:</b> Lars-Göran, Email</li><li><b>Phone:</b> 0700-318452</li><li><b>Date:</b> 2013-10-05 19:31:18</li></ul></div>
    </article>

    <article class="listing">
      <div class="photos">
        <div class="photo" role="img" aria-label="White ultralight with canopy open" style="width:150px;height:126px;background:linear-gradient(#a4acb4,#d8d8d8 60%,#6f7d56)"></div>
        <div class="side">
          <div class="photo" role="img" aria-label="Avionics instruments" style="width:78px;height:60px;background:linear-gradient(#d8d8d8,#777)"></div>
          <div class="photo" role="img" aria-label="Aircraft engine" style="width:78px;height:60px;background:linear-gradient(#c7c2b8,#4f6a66)"></div>
        </div>
      </div>
      <h2>VACUUM PUMP</h2>
      <p class="desc">Nordic Pump Works, TT 222 hrs, price 1200 SEK</p>
      <div class="seller"><svg class="avatar" role="img" aria-label="Seller"><use href="#user"/></svg>
        <ul><li><b>Name:</b> Lars-Göran, Email</li><li><b>Phone:</b> 0700-318452</li><li><b>Date:</b> 2013-10-05 19:31:18</li></ul></div>
    </article>
  </div>

  <div class="col col-2">
    <article class="listing">
      <div class="photos" style="margin-top:5px">
        <div class="photo" role="img" aria-label="Pilot beside white aircraft propeller" style="width:147px;height:177px;background:linear-gradient(#aeb6bc,#8a8f92 55%,#3a3a3a)"></div>
        <div class="side">
          <div class="photo" role="img" aria-label="Cockpit gauge" style="width:78px;height:85px;background:linear-gradient(#d6d8da,#9a9c9e)"></div>
          <div class="photo" role="img" aria-label="Instrument panel" style="width:78px;height:86px;background:linear-gradient(#666,#222)"></div>
        </div>
      </div>
      <h2>VACUUM PUMP</h2>
      <p class="desc">Nordic Pump Works, TT 222 hrs, price 1200 SEK</p>
      <div class="seller"><svg class="avatar" role="img" aria-label="Seller"><use href="#user"/></svg>
        <ul><li><b>Name:</b> Lars-Göran, Email</li><li><b>Phone:</b> 0700-318452</li><li><b>Date:</b> 2013-10-05 19:31:18</li></ul></div>
    </article>

    <article class="listing">
      <div class="photos">
        <div class="photo" role="img" aria-label="Red and white taildragger" style="width:147px;height:126px;background:linear-gradient(#c7c7c7,#b3403a 45%,#777)"></div>
        <div class="side">
          <div class="photo" role="img" aria-label="Pump components" style="width:78px;height:60px;background:linear-gradient(#ddd,#555)"></div>
          <div class="photo" role="img" aria-label="Instrument panel" style="width:78px;height:60px;background:linear-gradient(#666,#222)"></div>
        </div>
      </div>
      <h2>VACUUM PUMP</h2>
      <p class="desc">Nordic Pump Works, TT 222 hrs, price 1200 SEK</p>
      <div class="seller"><svg class="avatar" role="img" aria-label="Seller"><use href="#user"/></svg>
        <ul><li><b>Name:</b> Lars-Göran, Email</li><li><b>Phone:</b> 0700-318452</li><li><b>Date:</b> 2013-10-05 19:31:18</li></ul></div>
    </article>

    <article class="listing">
      <div class="photos">
        <div class="photo" role="img" aria-label="Blue and white biplane" style="width:147px;height:126px;background:linear-gradient(#a6b0b8,#4a86c0 50%,#6b7a52)"></div>
        <div class="side">
          <div class="photo" role="img" aria-label="Engine block" style="width:78px;height:60px;background:linear-gradient(#8c8c74,#4d4d40)"></div>
          <div class="photo" role="img" aria-label="Engine detail" style="width:78px;height:60px;background:linear-gradient(#3a7fa0,#3a2a22)"></div>
        </div>
      </div>
      <h2>VACUUM PUMP</h2>
      <p class="desc">Nordic Pump Works, TT 222 hrs, price 1200 SEK</p>
      <div class="seller"><svg class="avatar" role="img" aria-label="Seller"><use href="#user"/></svg>
        <ul><li><b>Name:</b> Lars-Göran, Email</li><li><b>Phone:</b> 0700-318452</li><li><b>Date:</b> 2013-10-05 19:31:18</li></ul></div>
    </article>
  </div>

  <div class="col col-3">
    <article class="listing">
      <div class="photos">
        <div class="photo" role="img" aria-label="Aircraft wing over landscape from the air" style="width:147px;height:126px;background:linear-gradient(#6d6a66,#b8b5b8 55%,#4c4a48)"></div>
        <div class="side">
          <div class="photo" role="img" aria-label="Parts laid out" style="width:78px;height:60px;background:linear-gradient(#d9d6d2,#888)"></div>
          <div class="photo" role="img" aria-label="Instrument panel" style="width:78px;height:60px;background:linear-gradient(#666,#222)"></div>
        </div>
      </div>
      <h2>VACUUM PUMP</h2>
      <p class="desc">Nordic Pump Works, TT 222 hrs, price 1200 SEK</p>
      <div class="seller"><svg class="avatar" role="img" aria-label="Seller"><use href="#user"/></svg>
        <ul><li><b>Name:</b> Lars-Göran, Email</li><li><b>Phone:</b> 0700-318452</li><li><b>Date:</b> 2013-10-05 19:31:18</li></ul></div>
    </article>

    <div class="promo" role="img" aria-label="Advertising banner: tablet giveaway"></div>

    <section class="news">
      <h3>Latest News</h3>
      <article><h4>Lorem ipsum dolor sit amet...</h4><p>Aliquam molestie, mi et imperdiet euismod, dui purus auctor tellus..</p></article>
      <article><h4>Lorem ipsum dolor sit amet...</h4><p>Aliquam molestie, mi et imperdiet euismod, dui purus auctor tellus..</p></article>
      <article><h4>Lorem ipsum dolor sit amet...</h4><p>Aliquam molestie, mi et imperdiet euismod, dui purus auctor tellus..</p></article>
    </section>

    <aside class="ads">
      <div class="ad"><a href="#">How to Make Electricity</a><p>Don't ever pay for electricity, you can make it simple &amp; cheap at home</p><small>HomePowerTips.org</small></div>
      <div class="ad"><a href="#">Prepare to be Shocked</a><p>Millions have already taken this amazing test. What's your real age?</p><small>AgeCheckr.com</small></div>
      <div class="ad"><a href="#">Make Solar Panel in 1 day</a><p>Make cheap homemade solar panels Cut Power Bill by 99%. $49 Kits</p><small>Sunroof-Panel-Guide.com</small></div>
      <span class="ad-choice"></span>
      <span class="ad-by">Ads by PlaceMint</span>
    </aside>
  </div>
</main>

<footer class="site-footer">
  <p class="copyright">Copyright © 2013 <span>Vingtorget Media.</span><br>All Right Reserved</p>
  <div class="follow">
    <p>Follow Us</p>
    <div class="social">
      <span role="img" aria-label="Social link one"></span>
      <span role="img" aria-label="Social link two"></span>
      <span role="img" aria-label="Social link three"></span>
      <span role="img" aria-label="News feed"></span>
    </div>
  </div>
</footer>

</body>
</html>
```